Vantiqo custom business card design

Need a authentic, innovative business card design for a new mobile app business. I am uploading a few screen images from our app for you to view. I would like app design theme to match business card design. I can also send logo images.

```html
<!DOCTYPE html>
<html lang="en">
<head>
<meta charset="utf-8">
<title>Vantiqo Business Card</title>
<link rel="stylesheet" href="https://fonts.googleapis.com/css2?family=Lato:wght@400;700;900&family=Arimo:wght@400;700&display=swap">
<style>
  :root {
    --backdrop: #7c4520;
    --card-purple: #62008c;
    --card-white: #ffffff;
    --ink-light: #ffffff;
    --ink-dark: #1e1e1e;
  }
  html, body {
    margin: 0;
    padding: 0;
    width: 1200px;
    height: 900px;
    overflow: hidden;
    background: var(--backdrop);
  }
  .stage {
    position: relative;
    width: 1200px;
    height: 900px;
  }
  .card {
    position: absolute;
    left: 330px;
    width: 556px;
    height: 344px;
    box-shadow: 2px 3px 6px rgba(0, 0, 0, 0.45);
  }
  .card-front {
    top: 90px;
    background: var(--card-purple);
    color: var(--ink-light);
    text-align: center;
    font-family: "Arimo", Arial, sans-serif;
  }
  .card-back {
    top: 469px;
    width: 559px;
    background: var(--card-white);
  }
  .holder-name {
    position: absolute;
    top: 62px;
    left: 0;
    right: 0;
    margin: 0;
    font-family: "Lato", sans-serif;
    font-weight: 700;
    font-size: 21px;
    letter-spacing: 0.3px;
    line-height: 24px;
  }
  .holder-role {
    position: absolute;
    top: 86px;
    left: 0;
    right: 0;
    margin: 0;
    font-size: 16.5px;
    line-height: 20px;
  }
  .rule {
    position: absolute;
    left: 180px;
    width: 195px;
    height: 1px;
    background: var(--ink-light);
  }
  .rule-top { top: 116px; }
  .rule-bottom { top: 221px; }
  .contact-list {
    position: absolute;
    top: 130px;
    left: 0;
    right: 0;
    margin: 0;
    padding: 0;
    list-style: none;
    font-size: 16.5px;
    line-height: 20px;
  }
  .contact-list b { font-weight: 700; }
  .address {
    position: absolute;
    top: 240px;
    left: 0;
    right: 0;
    margin: 0;
    font-style: normal;
    font-size: 16.5px;
    line-height: 20px;
  }
  .brand-mark {
    position: absolute;
    left: 197px;
    top: 58px;
    width: 166px;
    height: 166px;
    border-radius: 50%;
    background: var(--card-purple);
  }
  .brand-name {
    position: absolute;
    left: 0;
    right: 0;
    top: 230px;
    margin: 0;
    text-align: center;
    font-family: "Lato", sans-serif;
    font-weight: 900;
    font-size: 46px;
    line-height: 56px;
    color: var(--ink-dark);
  }
</style>
</head>
<body>
  <main class="stage">
    <section class="card card-front" aria-label="Business card front">
      <h1 class="holder-name">DANIEL HARLOW</h1>
      <p class="holder-role">Managing Director</p>
      <div class="rule rule-top"></div>
      <ul class="contact-list">
        <li><b>P:</b> 044-123 456 789</li>
        <li><b>M:</b> 044-123 456 789</li>
        <li><b>E:</b> info@webname.com</li>
        <li><b>W:</b> www.websitename.com</li>
      </ul>
      <div class="rule rule-bottom"></div>
      <address class="address">12345, Address Goes Here<br>Country Name, 123456.</address>
    </section>

    <section class="card card-back" aria-label="Business card back">
      <div class="brand-mark" aria-hidden="true"></div>
      <p class="brand-name">Vantiqo</p>
    </section>
  </main>
</body>
</html>
```